Generate website for parcelnook.com

Please design a website for our business. It must be clean, streamlined and obvious.

Our business combines ecommerce, with social networking, and zorvi maps. The logo is a shopping bag (ecommerce) and honeycombs inside representing the various compartments of business that are offered throughout site.

Clients use our site to visit the interior of stores and restaurants through video streaming and can virtually "walk through" the store and purchase items with friends and loved ones through the web.

We want to incorporate this logo with the work that we are doing and play on this honeycomb theme.

Our business is "parcelnook.com" because we are all about "u"!

Please make homepage with about us tab, contact us form, mission tab, we also want a page with our research links included that bolster the case for our startup.

We will incorporate a small video on the front screen. A homepage like fildrawer.com only this time with our parcelnook!

Also include, COMING SOON, on the homepage please.
Updates

These are some good templates/example sites of clean and simple but effective: https://7elmrow.com/preview www.fildrawer.com

We are excited to see your submissions. Currently, a very good and only one designer has posted so far. Let us know!

Please include the TM (trademark) symbol after the logo, the name, and the slogan throughout the website. Thank you!

Put the TM after the LOGO and after the slogan "Placement ran Supreme" Lorcan

Target Market(s)

We will begin with female online shoppers.

Industry/Entity Type

Shopping

Font styles to use
Serif
Sans Serif

Colors
e567a6
fece3e
85cae6

Requirements
Must have
• Clean Look
Simple like Fildrawer with simple options "see film" or login/signup.

With browser tabs at the bottom much like fildrawer.

1. Shopper when opening Parcelnook.com website will see a simple webpage with a large Parcelnook logo in the center.

2. User will see log-in and password or create account in upper right hand corner of webpage. Mobile device website will be underneath logo.

3.We Prefer a background for webpages adding a softer experience on the the eyes of the user. A photo in the background to show shopretail experience.

4. Clicking on theParcelnook logo will inform users of details and instructions about platform. Example: About, contact, mission, Help etc. Logo will become somewhat like an interactive tool for help and guidance.

5. Parcelnook is currently scouting for it's founding venues. A founding venue will be the first venues to appear to the public on the Parcelnook platform. Founding venues (FV) will inherit a lifetime of the lowest possible rates of 2%* for the duration of it's business. All businesses wishing to participate in the founding venues offer please leave your email address and store name and a representative will get back with you.

*Venues will be subjected to credit card and CoinTrail rates in addition.

Nice to have
• http://www.zorvi.com/patents/US5193774

Must include the link above/visual of this page on the site as well.

```html
<!DOCTYPE html>
<html lang="en">
<head>
<meta charset="utf-8">
<title>Parcelnook</title>
<link rel="stylesheet" href="https://fonts.googleapis.com/css2?family=Courgette&family=Jost:wght@400;600&family=Arimo&display=swap">
<style>
  :root {
    --mall-warm: #8a6f66;
    --mall-pink: #b98a97;
    --mall-floor: #7a5a4c;
    --band-white: rgba(250, 248, 248, 0.72);
    --panel-blue: #4f9cc9;
    --panel-lilac: #b9b3d2;
    --panel-grey: #dcd8dc;
    --ink-grey: #5e5e5e;
    --ink-dark: #1d1d1d;
    --white: #ffffff;
    --button-yellow: #e9e08a;
    --button-gold: #c9b454;
    --strip-slate: #4d6669;
    --footer-sky: #a3ddf6;
    --footer-sun: #fedb7c;
    --accent-pink: #e567a6;
    --coming-red: #d42a22;
  }
  * { box-sizing: border-box; margin: 0; padding: 0; }
  html, body { width: 1200px; height: 1091px; overflow: hidden; }
  body { position: relative; font-family: "Jost", sans-serif; background: var(--white); }

  .hero-photo {
    position: absolute; left: 0; top: 0; width: 1200px; height: 745px;
    background:
      radial-gradient(ellipse at 15% 45%, rgba(235, 170, 190, 0.7), transparent 45%),
      linear-gradient(180deg, var(--mall-warm) 0%, var(--mall-pink) 35%, #cdbdbd 60%, var(--mall-floor) 100%);
  }
  .hero-band {
    position: absolute; left: 0; top: 148px; width: 1200px; height: 515px;
    background: var(--band-white);
    box-shadow: 0 4px 10px rgba(0,0,0,0.35);
  }

  .brand { position: absolute; left: 0; top: 190px; width: 1200px; text-align: center; }
  .brand-mark {
    position: absolute; left: 345px; top: 10px; width: 110px; height: 110px;
    border-radius: 50%; background: var(--accent-pink);
  }
  .brand-name {
    position: absolute; left: 470px; top: 60px;
    font-weight: 600; font-size: 74px; line-height: 1; color: var(--ink-grey);
  }
  .brand-tagline {
    position: absolute; left: 0; top: 145px; width: 1234px;
    font-size: 26px; color: var(--ink-dark); letter-spacing: 0.3px;
  }

  .coming-soon {
    position: absolute; left: 1015px; top: 159px; width: 140px; height: 140px;
    border-radius: 50%;
    background: radial-gradient(circle at 40% 35%, #ffffff, #e3e1e3 70%, #c9c6c9);
    box-shadow: 0 2px 8px rgba(0,0,0,0.3);
    display: flex; align-items: center; justify-content: center;
    font-weight: 600; font-size: 20px; color: var(--coming-red); letter-spacing: -0.5px;
  }

  .action-panel {
    position: absolute; left: 149px; top: 385px; width: 939px; height: 270px;
    background: linear-gradient(180deg, var(--panel-blue) 0%, var(--panel-lilac) 45%, var(--panel-grey) 100%);
    opacity: 0.95;
  }
  .action-divider { position: absolute; left: 475px; top: 13px; width: 2px; height: 242px; background: var(--white); }
  .action-column { position: absolute; top: 0; width: 470px; text-align: center; }
  .action-column--shopper { left: 0; }
  .action-column--store { left: 469px; }
  .action-heading {
    margin-top: 12px; font-family: "Courgette", cursive;
    font-size: 37px; line-height: 55px; color: var(--white);
  }
  .action-box {
    position: absolute; left: 47px; top: 118px; width: 380px; height: 143px;
    border: 3px solid var(--white); border-radius: 12px;
  }
  .action-column--store .action-box { left: 49px; }
  .action-prompt {
    margin-top: 8px; font-family: "Courgette", cursive; font-size: 24px; color: var(--white);
  }
  .action-button {
    display: block; margin: 8px auto 0; width: 205px; height: 56px;
    border: 2px solid #b7a99a; border-radius: 3px;
    background: linear-gradient(180deg, #f3ec9f 0%, var(--button-yellow) 50%, var(--button-gold) 100%);
    box-shadow: 0 2px 3px rgba(0,0,0,0.35);
    font-family: "Courgette", cursive; font-size: 30px; color: var(--white);
    text-shadow: 0 1px 2px rgba(0,0,0,0.4);
  }

  .hero-strip { position: absolute; left: 0; top: 745px; width: 1200px; height: 15px; background: var(--strip-slate); }

  .site-footer {
    position: absolute; left: 0; top: 760px; width: 1200px; height: 331px;
    background: linear-gradient(160deg, var(--footer-sky) 15%, #d6e0c0 55%, var(--footer-sun) 85%);
  }
  .footer-nav { position: absolute; left: 70px; top: 85px; width: 205px; text-align: center; }
  .footer-nav a {
    display: block; font-family: "Arimo", sans-serif; font-size: 27px; line-height: 59.5px;
    color: var(--white); text-decoration: none;
  }
  .footer-rule { position: absolute; left: 63px; top: 277px; width: 1097px; height: 1px; background: #9e9e8c; }
  .footer-legal {
    position: absolute; left: 0; top: 288px; width: 1200px; text-align: center;
    font-size: 14px; color: var(--ink-dark);
  }
</style>
</head>
<body>
  <div class="hero-photo" role="img" aria-label="Softly blurred photo of a bright shopping mall interior with store fronts"></div>
  <div class="hero-band"></div>

  <header class="brand">
    <span class="brand-mark"></span>
    <h1 class="brand-name">Parcelnook</h1>
    <p class="brand-tagline">Visit any store you wish from you are !</p>
  </header>

  <div class="coming-soon">COMING SOON</div>

  <section class="action-panel">
    <div class="action-column action-column--shopper">
      <h2 class="action-heading">Sign up to join the<br>experience</h2>
      <div class="action-box">
        <p class="action-prompt">Visit a store</p>
        <button class="action-button" type="button">Signup/Login</button>
      </div>
    </div>
    <div class="action-divider"></div>
    <div class="action-column action-column--store">
      <h2 class="action-heading">Request or Become a<br>participating store</h2>
      <div class="action-box">
        <p class="action-prompt">Please leave your email</p>
        <button class="action-button" type="button" aria-label="Submit email"></button>
      </div>
    </div>
  </section>

  <div class="hero-strip"></div>

  <footer class="site-footer">
    <nav class="footer-nav">
      <a href="#about">About us</a>
      <a href="#mission">mission</a>
      <a href="#contact">Contact us</a>
    </nav>
    <div class="footer-rule"></div>
    <p class="footer-legal">under authorized use of Uspto # 5193774.</p>
  </footer>
</body>
</html>
```